White Paper and One-Page Advertisement for TELVORISH-QM

I need both documents to be better formatted and designed so they look professional, not something someone with mediocre word skills put together. They will go out to 1000s of industry professionals, and they need to look sharp. I need them to have my company's color palate logo, and branding on it similar to how it is now, but better. Please do not change any of the written content, but it can be arranged in any other format you think is better. Smart art and things i've already used can be omitted in favor of better designs. The developer is free to use their creativity. White paper should not be longer than the three pages unless necessary.

Target Market(s)

Life Sciences supply chain professionals

Colors
33b8a4
0592cd
9bcb3c
fbee3e
3277b5

Requirements
Must have
• Must be professional looking and not look like something done in word. Please use the color palate as seen on the documents.
Should not have
• Any changes to the written content.

```html
<!DOCTYPE html>
<html lang="en">
<head>
<meta charset="utf-8">
<title>TELVORISH-QM White Paper Spread</title>
<link href="https://fonts.googleapis.com/css2?family=Lato:ital,wght@0,400;0,700;0,900;1,400&display=swap" rel="stylesheet">
<style>
:root{
  --bg:#2b2b2d;
  --paper:#eef0f5;
  --ink:#2f3a44;
  --forest:#1f4638;
  --forest-deep:#163329;
  --lime:#9bcb3c;
  --teal:#33b8a4;
  --sea:#4a9a88;
  --blue:#3277b5;
  --sky:#0592cd;
  --cloud:#86bccb;
  --sage:#7aa06a;
}
*{box-sizing:border-box;margin:0;padding:0}
html,body{width:1200px;height:789px;overflow:hidden;background:var(--bg);font-family:"Lato",sans-serif;color:var(--ink)}
.spread{position:absolute;left:40px;top:40px;width:1120px;height:709px;display:flex;box-shadow:0 10px 30px rgba(0,0,0,.5)}
.page{position:relative;width:560px;height:100%;background:var(--paper);overflow:hidden;display:grid;grid-template-columns:1fr 1fr}
.page.left{border-right:1px solid #c9ccd4}
.page-top,.page-foot{position:absolute;left:0;width:100%;pointer-events:none}
.page-top{top:0;height:80px}
.page-foot{bottom:0;height:26px}
.col{position:relative;padding:86px 16px 36px;font-size:6.8px;line-height:1.45}
.col p{margin-bottom:5px}
.col.root{padding-top:68px}
.title-light{position:absolute;top:18px;left:16px;color:#fff;font-weight:900;font-size:20px}
.title-band{position:absolute;top:44px;left:10px;right:10px;font-weight:900;font-size:15px;color:#fff;text-align:right}
.title-dark{font-weight:900;font-size:16px;line-height:1.2;color:var(--sea);text-align:right;margin-bottom:10px}
h4{font-size:7.4px;font-weight:900;color:var(--forest);margin:6px 0 2px}
ul{padding-left:10px;margin-bottom:4px}
.stats{display:grid;grid-template-columns:repeat(4,1fr);gap:4px;margin:8px 0}
.stat{border-radius:3px;overflow:hidden;font-size:6px;color:var(--ink)}
.stat b{display:block;color:#fff;text-align:center;padding:3px 0;font-size:7px}
.stat span{display:block;padding:4px;min-height:40px}
.s1 b{background:var(--sage)}.s1 span{background:#c9dfa9}
.s2 b{background:var(--lime)}.s2 span{background:#dfe9c5}
.s3 b{background:var(--sea)}.s3 span{background:#c4ddd4}
.s4 b{background:var(--sky)}.s4 span{background:#c4dfea}
.callout{background:var(--forest);color:#fff;border-radius:12px;padding:6px 10px;font-weight:700;margin:6px 0}
.pills{display:grid;grid-template-columns:1fr 1fr;gap:6px 4px;margin:8px 0}
.pill{border-radius:10px;padding:5px 6px;color:#fff;font-weight:700;font-size:7px;text-align:center}
.p-lime{background:var(--lime)}.p-sea{background:var(--sea)}.p-cloud{background:var(--cloud)}
.bar{border-radius:0 12px 12px 0;color:#fff;font-weight:900;font-size:7px;padding:4px 8px;margin-top:5px}
.bar + p{margin:3px 0 0 4px}
.b-lime{background:var(--lime)}.b-sea{background:var(--sea)}.b-sky{background:var(--cloud)}.b-blue{background:var(--blue)}
.vision{background:var(--cloud);border-radius:40px;padding:14px 20px;color:#fff;font-weight:700;font-size:7.6px;line-height:1.5;margin:10px 0}
.vision h5{font-size:8px;margin-bottom:4px}
.vision ol{padding-left:12px}
</style>
</head>
<body>
<div class="spread">
  <section class="page left">
    <svg class="page-top" viewBox="0 0 560 80" preserveAspectRatio="none" aria-hidden="true">
      <path d="M0 0H560V70C470 40 360 34 250 58C170 74 80 66 0 50Z" fill="var(--forest)"/>
      <path d="M250 58C360 34 470 40 560 70V80C470 54 360 52 250 70Z" fill="var(--lime)"/>
    </svg>
    <svg class="page-foot" viewBox="0 0 560 26" preserveAspectRatio="none" aria-hidden="true">
      <path d="M0 10C200 0 380 4 560 14V26H0Z" fill="var(--forest)"/>
    </svg>
    <div class="col">
      <div class="title-light">Overview</div>
      <p>Surplus inventory is a challenge for every manufacturer. In the life sciences sector, unused materials and finished goods are often written off and destroyed, creating cost, compliance exposure and waste that is rarely measured across the supply chain as a whole.</p>
      <div class="stats">
        <div class="stat s1"><b>$70B</b><span>Surplus held across life science supply chains</span></div>
        <div class="stat s2"><b>$2.7B</b><span>Excess written off by leading firms each year</span></div>
        <div class="stat s3"><b>$1.0M</b><span>Average cost of a single disposal program</span></div>
        <div class="stat s4"><b>01</b><span>Compliant outlet for surplus in the market</span></div>
      </div>
      <p>Data reflects published industry reports and internal estimates reviewed with supply chain leaders.</p>
      <div class="callout">$1B in net income for firms is lost to write-down and disposal each year.</div>
      <p>Teams face competing priorities: service levels, regulatory constraints and cost control. Surplus builds when forecasts shift, processes vary and suppliers change terms.</p>
      <p>A life sciences marketplace and transaction standard for surplus would allow companies to trade materials safely, lower waste and recover value while meeting regulatory expectations.</p>
      <p>This paper reviews the current and future state of the industry and the path toward a compliant multi-vendor exchange.</p>
    </div>
    <div class="col">
      <div class="title-band">Baseline Problem</div>
      <h4>What?</h4>
      <ul><li>Excess raw materials and finished goods</li><li>Short shelf life and product changes</li><li>Limited compliant outlets for surplus</li></ul>
      <h4>Who?</h4>
      <ul><li>Life science manufacturers, suppliers and distributors</li></ul>
      <h4>Where &amp; When?</h4>
      <ul><li>At every stage of the product lifecycle, from launch to retirement</li></ul>
      <h4>How do we know it's there?</h4>
      <ul><li>Write-downs reported in annual statements</li></ul>
      <h4>Triple Bottom Line Impact</h4>
      <p>Financial, social and environmental costs grow as surplus is destroyed rather than reused by qualified buyers.</p>
      <h4>Current State</h4>
      <p>Surplus is handled case by case with brokers or disposal vendors, and data on volumes is rarely shared.</p>
      <div class="pills">
        <div class="pill p-lime">Forecast Accuracy</div>
        <div class="pill p-lime">Supplier Reliability</div>
        <div class="pill p-sea">Process Variability</div>
        <div class="pill p-cloud">External Environment</div>
      </div>
      <h4>Internal Solutions</h4>
      <p>Firms improve planning, tighten ordering and share forecasts, yet some surplus always remains.</p>
      <h4>Environmental Solutions</h4>
      <p>Recycling and donation programs help, but capacity is limited and documentation is heavy.</p>
    </div>
  </section>

  <section class="page right">
    <svg class="page-top" viewBox="0 0 560 80" preserveAspectRatio="none" aria-hidden="true">
      <path d="M0 0H560V40C450 30 380 50 300 60C200 70 90 52 0 40Z" fill="var(--forest)"/>
      <path d="M0 40C90 52 200 70 300 60V72C200 80 90 66 0 54Z" fill="var(--lime)"/>
    </svg>
    <svg class="page-foot" viewBox="0 0 560 26" preserveAspectRatio="none" aria-hidden="true">
      <path d="M0 14C180 4 380 0 560 10V26H0Z" fill="var(--forest)"/>
    </svg>
    <div class="col">
      <div class="title-band" style="text-align:left;top:40px">Undesirable Solutions</div>
      <p>Companies most often destroy surplus because it is simple and controlled, though costly and wasteful.</p>
      <h4>Refined Problem</h4>
      <p>There is no trusted, compliant exchange where surplus can move between qualified companies with full traceability.</p>
      <h4>Contemporary Operating Environment</h4>
      <ul><li>Rising regulatory scrutiny</li><li>Pressure to cut waste</li><li>Tighter margins</li></ul>
      <h4>Barriers</h4>
      <div class="bar b-lime">Compliance</div><p>Chain of custody must be proven for every lot.</p>
      <div class="bar b-lime">Liability</div><p>Sellers fear risk once material leaves their site.</p>
      <div class="bar b-sea">Economics</div><p>Recovery value must exceed handling cost.</p>
      <div class="bar b-sky">Sustainability</div><p>Few outlets measure their environmental impact.</p>
      <div class="bar b-blue">Confidence</div><p>Buyers need assurance of quality and origin.</p>
      <div class="bar b-lime">Confidence</div><p>Exchanges must be trusted by all partners.</p>
    </div>
    <div class="col root">
      <h2 class="title-dark">Root Cause &amp; Paradigm Shift</h2>
      <p>Manufacturers lack a shared platform built for regulated materials, so surplus defaults to disposal.</p>
      <h4>Future State</h4>
      <p>A compliant marketplace lets firms list, verify and transfer surplus with full records, turning waste into value.</p>
      <h4>Benefits</h4>
      <ul><li>Recovered value from unused stock</li><li>Lower disposal volumes and cost</li><li>Verified traceability for each lot</li><li>Support for sustainability goals</li></ul>
      <div class="vision">
        <h5>Vision</h5>
        <ol>
          <li>A collaborative and compliant multi-vendor marketplace is part of Pharma's normal operating practices</li>
          <li>Waste is not tolerated in the life sciences industry</li>
          <li>There is always a compliant outlet</li>
        </ol>
      </div>
      <h4>How to Implement</h4>
      <ul><li>Align partners on shared standards</li><li>Qualify buyers and sellers</li><li>Launch with pilot categories</li></ul>
      <h4>Data Integrity</h4>
      <p>Every transaction is recorded with batch data, storage history and documents so quality teams can release material with confidence. TELVORISH-QM supports this standard.</p>
    </div>
  </section>
</div>
</body>
</html>
```